Anesthesia Medical Practice Business Card

We need a business card to hand out to surgeons with my basic information. Something that stands out but is not over the top. The medical community is rather conservative. I'd like them to call me first when flipping through their rolodex of anesthesiologists. I'd like the card to communicate confidence, control, professionalism yet serenity. I don't want the card to be pricey to print.

he logo will be provided as a vector graphic in addition to a complete business card design including the logo

Lem Varo Keshtel, M.D.
Board Certified Anesthesiologist

(555) 386-2157

lkeshtel@quorvanmail.example

Mailing Address:
47315 Brindlecove Ave.
Suite 382-6475
Los Angeles, CA 90877

A logo that inegrates my initials perhaps
LK MD
My initials are LK and MD as in Medical Doctor

or
perhaps a physician in surgical mask and cap caring for a patient

Target Market(s)

Surgeons who need anesthesia services

Industry/Entity Type

Medical

Requirements
Must have
• the logo will be provided as a vector graphic in addition to a complete business card design including the logo

Lem Varo Keshtel, M.D.

(555) 386-2157

lkeshtel@quorvanmail.example

Mailing Address:
47315 Brindlecove Ave.
Suite 382-6475
Los Angeles, CA 90877

Nice to have
• A logo that inegrates my initials perhaps
LK MD

or

```html
<!DOCTYPE html>
<html lang="en">
<head>
<meta charset="utf-8">
<title>Lem Varo Keshtel, M.D. — Business Card</title>
<link href="https://fonts.googleapis.com/css2?family=Josefin+Sans:wght@300;400&display=swap" rel="stylesheet">
<style>
  :root {
    --backdrop: #3a302b;
    --card: #45504b;
    --card-light: #4e5a55;
    --ink: #f4f2ec;
    --ink-soft: #d9ddd8;
  }
  html, body {
    margin: 0;
    width: 1200px;
    height: 1000px;
    overflow: hidden;
    background: var(--backdrop);
  }
  .stage {
    width: 1200px;
    height: 1000px;
    display: flex;
    align-items: center;
    justify-content: center;
  }
  .business-card {
    position: relative;
    width: 840px;
    height: 480px;
    background: linear-gradient(135deg, var(--card) 0%, var(--card-light) 55%, var(--card) 100%);
    color: var(--ink);
    font-family: "Josefin Sans", sans-serif;
    box-shadow: 0 18px 40px rgba(0,0,0,0.45);
  }
  .mark {
    position: absolute;
    left: 520px;
    top: 90px;
    display: flex;
    align-items: center;
    gap: 14px;
    font-size: 64px;
    font-weight: 400;
    letter-spacing: 4px;
    color: var(--ink);
  }
  .mark-square {
    width: 14px;
    height: 14px;
    background: var(--ink);
  }
  .details {
    position: absolute;
    left: 520px;
    top: 210px;
    line-height: 1.45;
  }
  .name {
    margin: 0;
    font-size: 22px;
    font-weight: 400;
    letter-spacing: 0.5px;
  }
  .title {
    margin: 0 0 18px;
    font-size: 13px;
    font-weight: 300;
    color: var(--ink-soft);
  }
  .contact, .address {
    margin: 0 0 14px;
    font-size: 13px;
    font-weight: 300;
    color: var(--ink-soft);
    font-style: normal;
  }
</style>
</head>
<body>
  <main class="stage">
    <section class="business-card">
      <div class="mark"><span class="mark-square"></span>LK</div>
      <div class="details">
        <h1 class="name">Lem Varo Keshtel, M.D.</h1>
        <p class="title">Board Certified Anesthesiologist</p>
        <p class="contact">(555) 386-2157<br>lkeshtel@quorvanmail.example</p>
        <address class="address">Mailing Address:<br>47315 Brindlecove Ave.<br>Suite 382-6475<br>Los Angeles, CA 90877</address>
      </div>
    </section>
  </main>
</body>
</html>
```